Wealth Education Business Needs Sharp Business Card Design

We need a business card design for a recently launched investor education business called Harbor Crest.

The final design should promote security, empowerment, self improvement and financial gain. The card will ideally promote the stature of the business.

For more information and colours please visit harborcrest.com.au

Target Market(s)

Corporate executives and high net worth individuals

Industry/Entity Type

Education

Contact Information for Business Card

```html
<!DOCTYPE html>
<html lang="en">
<head>
<meta charset="utf-8">
<title>Harbor Crest Business Card</title>
<link href="https://fonts.googleapis.com/css2?family=Lato:wght@400;700&display=swap" rel="stylesheet">
<style>
  :root {
    --canvas: #e7e8e9;
    --card-front: #ffffff;
    --card-back-top: #474747;
    --card-back-bottom: #2f2f2f;
    --ink: #1e1e1e;
    --teal: #17888a;
    --green-dark: #5c993b;
    --green-light: #7db24f;
    --white: #ffffff;
    --muted: #c9c9c9;
  }
  * { margin: 0; padding: 0; box-sizing: border-box; }
  html, body { width: 1200px; height: 720px; overflow: hidden; }
  body {
    background: var(--canvas);
    font-family: "Lato", sans-serif;
    position: relative;
  }
  .card {
    position: absolute;
    top: 241px;
    width: 419px;
    height: 239px;
    border-radius: 14px;
    overflow: hidden;
  }
  .card-front { left: 148px; background: var(--card-front); }
  .card-back {
    left: 633px;
    background: linear-gradient(160deg, var(--card-back-top), var(--card-back-bottom));
  }
  .brand-name {
    font-family: "Lato", sans-serif;
    font-weight: 700;
    text-transform: uppercase;
    white-space: nowrap;
  }
  .front-brand {
    position: absolute;
    left: 21px;
    top: 36px;
    font-size: 19px;
    letter-spacing: 3px;
    color: var(--ink);
  }
  .person {
    position: absolute;
    right: 18px;
    top: 36px;
    text-align: right;
  }
  .person-name { font-size: 16px; font-weight: 700; color: var(--teal); line-height: 1.1; }
  .person-role { font-size: 11.5px; color: var(--ink); margin-top: 3px; }
  .address {
    position: absolute;
    left: 21px;
    top: 98px;
    font-size: 12.5px;
    line-height: 15px;
    font-weight: 700;
    color: var(--ink);
  }
  .contact-band {
    position: absolute;
    left: 0;
    bottom: 0;
    width: 100%;
    height: 89px;
    background: linear-gradient(90deg, var(--green-dark), var(--green-light));
  }
  .contact-list {
    position: absolute;
    left: 18px;
    top: 11px;
    list-style: none;
    color: var(--white);
    font-size: 12px;
    line-height: 14.5px;
  }
  .contact-list li { display: flex; align-items: center; gap: 5px; }
  .contact-list svg { width: 10px; height: 10px; flex: none; }
  .back-brand {
    position: absolute;
    left: 0;
    width: 100%;
    top: 100px;
    text-align: center;
    font-size: 34px;
    letter-spacing: 7px;
    color: var(--white);
  }
  .back-url {
    position: absolute;
    left: 0;
    width: 100%;
    top: 209px;
    text-align: center;
    font-size: 12px;
    color: var(--muted);
  }
</style>
</head>
<body>
  <section class="card card-front" aria-label="Business card front">
    <div class="brand-name front-brand">Harbor Crest</div>
    <div class="person">
      <div class="person-name">Marcus Reid</div>
      <div class="person-role">Director</div>
    </div>
    <address class="address" style="font-style:normal">
      Level 5, 27 Quayside Row<br>
      Melbourne VIC 3000
    </address>
    <div class="contact-band">
      <ul class="contact-list">
        <li>
          <svg viewBox="0 0 10 10" aria-hidden="true"><path d="M1 3 Q5 0 9 3 L8 4.5 L6.5 3.8 L6.5 3 Q5 2.6 3.5 3 L3.5 3.8 L2 4.5 Z M2.5 5 H7.5 L8.5 9 H1.5 Z" fill="currentColor"/></svg>
          1300 555 017
        </li>
        <li>
          <svg viewBox="0 0 10 10" aria-hidden="true"><rect x="2.5" y="0.5" width="5" height="9" rx="1" fill="none" stroke="currentColor"/><circle cx="5" cy="8" r="0.6" fill="currentColor"/></svg>
          +613 5550 1284
        </li>
        <li>
          <svg viewBox="0 0 10 10" aria-hidden="true"><rect x="0.5" y="2" width="9" height="6" fill="currentColor"/><path d="M0.5 2 L5 5.5 L9.5 2" fill="none" stroke="#6aa545" stroke-width="0.9"/></svg>
          support@harborcrest.com.au
        </li>
        <li>
          <svg viewBox="0 0 10 10" aria-hidden="true"><circle cx="5" cy="5" r="4.3" fill="none" stroke="currentColor"/><ellipse cx="5" cy="5" rx="1.8" ry="4.3" fill="none" stroke="currentColor" stroke-width="0.8"/><path d="M0.7 5 H9.3" stroke="currentColor" stroke-width="0.8"/></svg>
          www.harborcrest.com.au
        </li>
      </ul>
    </div>
  </section>

  <section class="card card-back" aria-label="Business card back">
    <div class="brand-name back-brand">Harbor Crest</div>
    <div class="back-url">www.harborcrest.com.au</div>
  </section>
</body>
</html>
```